Business card for medical clinic

I need an upmarket, modern medical/health business card for my clinic

Contact Information for Business Card

name, address, email, qr code

```html
<!DOCTYPE html>
<html lang="en">
<head>
<meta charset="utf-8">
<title>Halewood Health Clinic – Business Card</title>
<link rel="stylesheet" href="https://fonts.googleapis.com/css2?family=Tinos:wght@400;700&display=swap">
<style>
  :root {
    --backdrop: #2b2c2e;
    --brand-blue: #1f9fd9;
    --brand-blue-deep: #1a8fca;
    --navy: #17324f;
    --card-white: #f7f7f7;
    --card-grey: #e4e4e4;
    --ink: #2a2a2a;
    --rule: #8a8a8a;
  }
  * { box-sizing: border-box; margin: 0; padding: 0; }
  html, body {
    width: 1200px; height: 900px; overflow: hidden;
    background: var(--backdrop);
    font-family: "Tinos", "Times New Roman", serif;
  }
  .canvas { position: relative; width: 1200px; height: 900px; }

  .card {
    position: absolute;
    width: 700px; height: 400px;
    border-radius: 34px;
    box-shadow: 0 14px 30px rgba(0,0,0,.45);
    overflow: hidden;
  }

  /* Back side */
  .card--back {
    left: 90px; top: 50px;
    background: linear-gradient(100deg, var(--brand-blue-deep) 0%, var(--brand-blue) 60%, #24a8e0 100%);
    display: flex; align-items: center; justify-content: center;
  }
  .brand {
    display: flex; align-items: center; gap: 16px;
  }
  .brand__dot {
    width: 22px; height: 22px; border-radius: 50%; flex: none;
  }
  .brand__name {
    font-size: 34px; font-weight: 700; letter-spacing: 3px;
    text-transform: uppercase; white-space: nowrap;
  }
  .card--back .brand__dot { background: #ffffff; }
  .card--back .brand__name { color: #ffffff; }

  /* Front side */
  .card--front {
    left: 410px; top: 460px;
    background: linear-gradient(115deg, var(--card-grey) 0%, var(--card-white) 45%, #ffffff 100%);
  }
  .card--front .brand {
    position: absolute; left: 52px; top: 64px;
  }
  .card--front .brand__dot { background: var(--brand-blue); }
  .card--front .brand__name { color: var(--navy); font-size: 30px; }

  .details {
    position: absolute; left: 0; right: 40px; bottom: 58px;
    display: flex; align-items: flex-end; justify-content: flex-end;
  }
  .person {
    text-align: right; padding-right: 22px;
  }
  .person__role { font-size: 18px; color: var(--ink); }
  .person__name {
    font-size: 24px; color: var(--brand-blue);
    text-transform: uppercase; letter-spacing: .5px; margin-top: 2px;
  }
  .divider {
    width: 1px; height: 132px; background: var(--rule);
  }
  .contacts {
    list-style: none; padding-left: 20px;
    display: flex; flex-direction: column; gap: 9px;
  }
  .contacts li {
    display: flex; align-items: center; gap: 10px;
    font-size: 17px; color: var(--ink); white-space: nowrap;
  }
  .contacts svg { width: 18px; height: 18px; flex: none; fill: var(--brand-blue); }
</style>
</head>
<body>
<main class="canvas">

  <section class="card card--back" aria-label="Business card back">
    <div class="brand">
      <span class="brand__dot"></span>
      <span class="brand__name">Halewood Health Clinic</span>
    </div>
  </section>

  <section class="card card--front" aria-label="Business card front">
    <div class="brand">
      <span class="brand__dot"></span>
      <span class="brand__name">Halewood Health Clinic</span>
    </div>

    <div class="details">
      <div class="person">
        <p class="person__role">Director</p>
        <p class="person__name">Daniel Reyes</p>
      </div>
      <div class="divider"></div>
      <ul class="contacts">
        <li>
          <svg viewBox="0 0 24 24" aria-hidden="true"><path d="M6.6 10.8a15.1 15.1 0 0 0 6.6 6.6l2.2-2.2a1 1 0 0 1 1-.25 11.4 11.4 0 0 0 3.6.57 1 1 0 0 1 1 1V20a1 1 0 0 1-1 1A17 17 0 0 1 3 4a1 1 0 0 1 1-1h3.5a1 1 0 0 1 1 1c0 1.25.2 2.45.57 3.57a1 1 0 0 1-.25 1z"/></svg>
          310-450-7200
        </li>
        <li>
          <svg viewBox="0 0 24 24" aria-hidden="true"><path d="M2 5h20v14H2zm2 2v.4l8 5.1 8-5.1V7zm0 2.8V17h16V9.8l-8 5.1z"/></svg>
          info@halewoodhealthclinic.com
        </li>
        <li>
          <svg viewBox="0 0 24 24" aria-hidden="true"><path d="M12 2a10 10 0 1 0 0 20 10 10 0 0 0 0-20zm6.9 6h-3a15 15 0 0 0-1.3-3.9A8 8 0 0 1 18.9 8zM12 4c.8 1.1 1.5 2.5 1.9 4h-3.8c.4-1.5 1.1-2.9 1.9-4zM4.3 14a8 8 0 0 1 0-4h3.4a16 16 0 0 0 0 4zm.8 2h3a15 15 0 0 0 1.3 3.9A8 8 0 0 1 5.1 16zm3-8h-3a8 8 0 0 1 4.3-3.9A15 15 0 0 0 8.1 8zM12 20c-.8-1.1-1.5-2.5-1.9-4h3.8c-.4 1.5-1.1 2.9-1.9 4zm2.3-6H9.7a14 14 0 0 1 0-4h4.6a14 14 0 0 1 0 4zm.3 5.9a15 15 0 0 0 1.3-3.9h3a8 8 0 0 1-4.3 3.9zm1.7-5.9a16 16 0 0 0 0-4h3.4a8 8 0 0 1 0 4z"/></svg>
          www.halewoodhealthclinic.com
        </li>
        <li>
          <svg viewBox="0 0 24 24" aria-hidden="true"><path d="M12 2a7 7 0 0 0-7 7c0 5.2 7 13 7 13s7-7.8 7-13a7 7 0 0 0-7-7zm0 9.5A2.5 2.5 0 1 1 12 6.5a2.5 2.5 0 0 1 0 5z"/></svg>
          12 Harbor Lane, Eastport 4021
        </li>
      </ul>
    </div>
  </section>

</main>
</body>
</html>
```